Business Cards Design for the electrical wholesaler: clean bold dynamic :)

We need a business card design that would follow our latest brand guidelines. As an electrical wholesaler we want to bring a fresh look and feel into the industry. The design should be clean bold and dynamic. It should come alive with the renewed energy of our green colour. Our grey colour should keep things balanced and complement the notion of maturity and responsibility. We employ Lato as a corporate font however are not bound by this font and we’re open to interpretation here.

Target Market(s)

Electrical contractors

Industry/Entity Type

Business

Contact Information for Business Card

Logo
Name & Surname: Halyna Dorosh
Job Title: Director of Marketing
Email: halya.dorosh@quillmail.example
Cell phone: XXX.XXX.XXXX
Address: 20517 - 87 Ave. Edmonton, AB, Canada. T6K 4N8
Business Phone: 780.555.0184
Website: www.brovix.example

Font styles to use
Other font styles liked:
• Lato

Requirements
Must have
• Logo & website
Nice to have
• Brand elements - some of them you may find in the attached Brand Guidelines (e.g. three lines on the background signifying "W")

```html
<!DOCTYPE html>
<html lang="en">
<head>
<meta charset="utf-8">
<title>Brovix Business Cards</title>
<link rel="stylesheet" href="https://fonts.googleapis.com/css2?family=Lato:wght@400;700&display=swap">
<style>
  :root {
    --brand-green: #6cc20a;
    --brand-green-deep: #58a806;
    --brand-grey: #3f4042;
    --brand-dark: #2b2b2d;
    --card-white: #ffffff;
    --canvas-bg: #ececec;
    --text-grey: #2f3032;
  }
  * { box-sizing: border-box; margin: 0; padding: 0; }
  html, body {
    width: 1200px;
    height: 800px;
    overflow: hidden;
    background: var(--canvas-bg);
    font-family: "Lato", sans-serif;
  }
  .canvas {
    position: relative;
    width: 1200px;
    height: 800px;
  }
  .card {
    position: absolute;
    top: 250px;
    width: 525px;
    height: 300px;
    border-radius: 4px;
    overflow: hidden;
    box-shadow: 0 6px 18px rgba(0,0,0,0.14);
  }
  /* Back side */
  .card-back {
    left: 50px;
    background: var(--brand-green);
  }
  .card-back .backdrop {
    position: absolute;
    inset: 0;
    background: linear-gradient(135deg, var(--brand-green-deep) 0%, var(--brand-green) 55%, #74c812 100%);
  }
  .card-back .wordmark {
    position: absolute;
    left: 0; right: 0;
    top: 108px;
    text-align: center;
    font-weight: 700;
    font-size: 64px;
    letter-spacing: 1px;
    color: var(--brand-grey);
  }
  .card-back .website {
    position: absolute;
    right: 28px;
    bottom: 26px;
    color: var(--card-white);
    font-size: 15px;
    letter-spacing: 1px;
  }
  /* Front side */
  .card-front {
    left: 625px;
    background: var(--card-white);
  }
  .card-front .identity {
    position: absolute;
    left: 36px;
    top: 38px;
  }
  .identity .person-name {
    font-size: 24px;
    font-weight: 400;
    color: var(--text-grey);
  }
  .identity .job-title {
    font-size: 15px;
    color: var(--brand-green);
    margin-top: 2px;
  }
  .contact-list {
    position: absolute;
    left: 36px;
    top: 138px;
    list-style: none;
    font-size: 13.5px;
    line-height: 1.45;
    color: var(--text-grey);
  }
  .contact-list li {
    display: flex;
    align-items: flex-start;
    gap: 8px;
    margin-bottom: 3px;
  }
  .contact-list svg {
    flex: none;
    width: 12px;
    height: 14px;
    margin-top: 2px;
    fill: var(--brand-green);
  }
  .card-front .wordmark {
    position: absolute;
    right: 36px;
    top: 92px;
    font-weight: 700;
    font-size: 46px;
    color: var(--brand-grey);
  }
  .card-front .footer-shape {
    position: absolute;
    left: 0;
    bottom: 0;
    width: 525px;
    height: 300px;
  }
  .card-front .website {
    position: absolute;
    right: 26px;
    bottom: 16px;
    color: var(--brand-green);
    font-size: 15px;
    letter-spacing: 1px;
  }
</style>
</head>
<body>
<main class="canvas">

  <section class="card card-back" aria-label="Business card back">
    <div class="backdrop" role="img" aria-label="Green background with fine vertical stripe pattern"></div>
    <div class="wordmark">brovix</div>
    <div class="website">www.<strong>brovix</strong>.example</div>
  </section>

  <section class="card card-front" aria-label="Business card front">
    <svg class="footer-shape" viewBox="0 0 525 300" aria-hidden="true">
      <path d="M0,244 L0,256 L318,262 C334,262 340,250 352,247 Z" fill="var(--brand-green)"/>
      <path d="M0,262 L320,268 C342,268 348,246 372,244 L525,244 L525,300 L0,300 Z" fill="var(--brand-dark)"/>
    </svg>

    <div class="identity">
      <h1 class="person-name">Halyna Dorosh</h1>
      <p class="job-title">Director of Marketing</p>
    </div>

    <ul class="contact-list">
      <li>
        <svg viewBox="0 0 12 16"><path d="M6 0C2.7 0 0 2.6 0 5.8 0 10 6 16 6 16s6-6 6-10.2C12 2.6 9.3 0 6 0zm0 8.2A2.3 2.3 0 1 1 6 3.6a2.3 2.3 0 0 1 0 4.6z"/></svg>
        <span>20517 - 87 Ave. Edmonton,<br>AB, Canada. T6K 4N8</span>
      </li>
      <li>
        <svg viewBox="0 0 12 16"><path d="M2 0h8a2 2 0 0 1 2 2v12a2 2 0 0 1-2 2H2a2 2 0 0 1-2-2V2a2 2 0 0 1 2-2zm0 2v10h8V2H2zm4 11a1 1 0 1 0 0 2 1 1 0 0 0 0-2z"/></svg>
        <span>780.555.0184</span>
      </li>
      <li>
        <svg viewBox="0 0 14 12"><path d="M0 1h14v10H0V1zm1.5 1.5L7 7l5.5-4.5v-.2h-11v.2z"/></svg>
        <span>halya.dorosh@quillmail.example</span>
      </li>
    </ul>

    <div class="wordmark">brovix</div>
    <div class="website">www.<strong>brovix</strong>.example</div>
  </section>

</main>
</body>
</html>
```